Tolbek cards

I want a simple business card that pops.
Logo on one side.
On side two i want.
"Are you thinking about a new building on your property, or renovating an existing structure? Contact".....
Owners Name: Dale Whitacre
Owners Phone number: 610-555-0187
Address:4076 Copper Ridge RD, Marlow Falls, VT 05399
Committed to Quality, Service, and Integrity

```html
<!DOCTYPE html>
<html lang="en">
<head>
<meta charset="utf-8">
<title>Tolbek Builders LLC – Business Card</title>
<link href="https://fonts.googleapis.com/css2?family=Montserrat:wght@300;400;600;800&family=Pinyon+Script&display=swap" rel="stylesheet">
<style>
  :root {
    --brown: #412c1c;
    --white: #ffffff;
    --ink: #1c1c1c;
    --stage: #d6d6d6;
  }
  * { box-sizing: border-box; margin: 0; padding: 0; }
  html, body { width: 1200px; height: 800px; overflow: hidden; }
  body {
    background: var(--stage);
    font-family: "Montserrat", Arial, sans-serif;
    display: flex;
    align-items: center;
    justify-content: center;
    gap: 40px;
  }
  .card {
    position: relative;
    width: 560px;
    height: 320px;
    border-radius: 22px;
    overflow: hidden;
  }

  /* Contact side */
  .card--contact { background: var(--white); color: var(--ink); }
  .headline { position: absolute; left: 30px; top: 26px; width: 480px; }
  .headline__script {
    font-family: "Pinyon Script", cursive;
    font-size: 36px;
    line-height: 1;
  }
  .headline__bold {
    font-weight: 800;
    font-size: 17px;
    margin-top: 8px;
    letter-spacing: 0.2px;
    white-space: nowrap;
  }
  .headline__bold .light { font-weight: 400; }
  .headline__light {
    font-weight: 300;
    font-size: 17px;
    margin-top: 3px;
    letter-spacing: 0.6px;
    white-space: nowrap;
  }
  .accent-bar {
    position: absolute;
    right: 0;
    top: 0;
    width: 40px;
    height: 110px;
    background: var(--brown);
  }
  .brand-mark {
    position: absolute;
    right: 30px;
    top: 170px;
    font-weight: 800;
    font-size: 40px;
    color: var(--brown);
    letter-spacing: 1px;
  }
  .contact-block {
    position: absolute;
    left: 0;
    top: 150px;
    width: 330px;
    height: 142px;
    background: var(--brown);
    color: var(--white);
    padding: 14px 0 0 30px;
  }
  .contact-block__label {
    font-size: 13px;
    font-weight: 400;
    display: flex;
    align-items: center;
    gap: 10px;
  }
  .contact-block__label::after {
    content: "";
    display: block;
    width: 130px;
    height: 1px;
    background: var(--white);
  }
  .contact-block__name {
    font-weight: 800;
    font-size: 21px;
    margin: 2px 0 8px;
    letter-spacing: 0.5px;
  }
  .contact-line {
    display: flex;
    align-items: flex-start;
    gap: 8px;
    font-size: 14px;
    line-height: 1.3;
    margin-bottom: 4px;
  }
  .contact-line svg { flex: none; margin-top: 1px; }

  /* Brand side */
  .card--brand {
    background: var(--brown);
    color: var(--white);
    display: flex;
    align-items: center;
    justify-content: center;
    gap: 18px;
  }
  .brand-lockup__square {
    width: 64px;
    height: 64px;
    background: var(--white);
  }
  .brand-lockup__text { font-weight: 800; line-height: 1; }
  .brand-lockup__name { font-size: 66px; letter-spacing: 1px; }
  .brand-lockup__sub { font-size: 24px; letter-spacing: 1.5px; margin-top: 4px; }
</style>
</head>
<body>

  <section class="card card--contact" aria-label="Contact side">
    <div class="headline">
      <p class="headline__script">Are you thinking about</p>
      <p class="headline__bold">A NEW BUILDING ON YOUR PROPERTY,<span class="light"> OR</span></p>
      <p class="headline__light">RENOVATING AN EXISTING STRUCTURE?</p>
    </div>

    <div class="accent-bar"></div>
    <p class="brand-mark">Tolbek</p>

    <div class="contact-block">
      <p class="contact-block__label">Contact</p>
      <p class="contact-block__name">DALE WHITACRE</p>
      <p class="contact-line">
        <svg width="16" height="16" viewBox="0 0 16 16" aria-hidden="true">
          <circle cx="8" cy="8" r="8" fill="#fff"/>
          <path d="M5.2 4.2l1.4-.4.9 2-1 .8a5 5 0 0 0 2.7 2.7l.8-1 2 .9-.4 1.4c-3.7.2-6.6-2.7-6.4-6.4z" fill="#412c1c"/>
        </svg>
        610-555-0187
      </p>
      <p class="contact-line">
        <svg width="16" height="16" viewBox="0 0 16 16" aria-hidden="true">
          <circle cx="8" cy="8" r="8" fill="#fff"/>
          <path d="M8 3.5a3 3 0 0 0-3 3c0 2.2 3 5.8 3 5.8s3-3.6 3-5.8a3 3 0 0 0-3-3z" fill="#412c1c"/>
          <circle cx="8" cy="6.5" r="1.1" fill="#fff"/>
        </svg>
        <span>4076 Copper Ridge RD,<br>Marlow Falls, VT 05399</span>
      </p>
    </div>
  </section>

  <section class="card card--brand" aria-label="Brand side">
    <div class="brand-lockup__square"></div>
    <div class="brand-lockup__text">
      <p class="brand-lockup__name">TOLBEK</p>
      <p class="brand-lockup__sub">BUILDERS LLC</p>
    </div>
  </section>

</body>
</html>
```